Musician looking for catchy Web Design for promotion

My name is Brenna Coyle. I'm an Irish musician who plays the tin whistle and the flute. I'm also the leader of a traditional Irish music and dance ensemble called Gather the Willows (www.gatherthewillows-example.com) and for the past 30 years, I've toured the world performing thousands of concerts. I run an annual cruise (www.brennacoylevoyage-example.com) that I would like a link to, and I'm also I'm organizing tours to Ireland that I would like a page set up for. I'm looking for a website to promote my tours and my music.
Updates

Hello Graphic Designers, I am only looking for the design of the home page to make my decision. Thank you. Brenna

Target Market(s)

Music fans of Irlsh and World Music

Industry/Entity Type

Entertainment Industry

Number of Pages Required

5+ page

Requirements
Must have
• I'm looking for a catchy design that shows a photo of me. I would like a few links....
• BIO
• TOURDATES
• BRENNA COYLE CRUISE
• MUSICAL TOUR OF IRELAND
• CONTACT
• VIDEO
• GALLERY
• CONTACT
• MAILING LIST
• STORE
Nice to have
• we'll see!

```html
<!DOCTYPE html>
<html lang="en">
<head>
<meta charset="utf-8">
<title>Brenna Coyle's Musical Tour of Ireland</title>
<link rel="stylesheet" href="https://fonts.googleapis.com/css2?family=Kalam:wght@300;400&family=Open+Sans:ital,wght@0,400;0,600;0,700;1,400&display=swap">
<style>
:root{
  --orange:#f7941d;
  --orange-dark:#e07b00;
  --ink:#1a1a1a;
  --panel:#2b2b2b;
  --panel-2:#333;
  --black:#050505;
  --text:#e6e6e6;
  --muted:#bdbdbd;
  --white:#fff;
  --row-a:#f1f1f1;
  --row-b:#dcdcdc;
}
*{box-sizing:border-box;margin:0;padding:0}
html,body{width:1200px;height:3364px;overflow:hidden}
body{background:var(--ink);font-family:"Open Sans",Arial,sans-serif;color:var(--text);font-size:13px}
.wrap{width:1002px;margin:0 auto;position:relative}
.accent{color:var(--orange)}
.btn{display:inline-block;background:var(--orange);color:#111;font-weight:700;font-size:13px;padding:9px 18px;border-radius:2px}

/* header */
.site-header{height:100px;background:linear-gradient(#4a4a4a,#1e1e1e)}
.site-header .wrap{display:flex;align-items:center;height:100px}
.brand{display:flex;align-items:center;gap:12px;color:var(--white);font-size:15px;font-weight:600;letter-spacing:.3px}
.brand-mark{width:44px;height:44px;border-radius:50%;background:#8a8a8a}
.header-right{margin-left:auto;display:flex;align-items:center;gap:22px}
.phone{display:flex;align-items:center;gap:10px;color:var(--white);font-size:20px}
.phone-ico{width:34px;height:34px;border:2px solid var(--orange);border-radius:50%;display:flex;align-items:center;justify-content:center}
.follow{font-family:"Kalam",cursive;font-weight:300;color:var(--orange);font-size:28px;display:flex;align-items:center;gap:8px}
.social{width:24px;height:24px;border-radius:50%;background:var(--white)}
.book-btn{background:var(--orange);color:#111;font-weight:600;font-size:13px;padding:9px 16px;border-radius:16px}

.main-nav{height:40px;background:linear-gradient(var(--orange),var(--orange-dark))}
.main-nav ul{list-style:none;display:flex;height:40px;width:1002px;margin:0 auto}
.main-nav li{flex:auto;text-align:center;line-height:40px;color:#1a1a1a;font-size:13px}
.main-nav li.current{background:#333;color:var(--white);font-weight:600;flex:0 0 76px}

/* hero */
.hero{height:522px;position:relative;background:linear-gradient(170deg,#c96a1a 0%,#a7401a 35%,#6e2310 70%,#2a0e05 100%)}
.hero-caption{position:absolute;left:50%;top:318px;transform:translateX(-50%);padding:8px 22px;background:rgba(30,20,15,.7);text-align:center;color:var(--white);white-space:nowrap}
.hero-caption h1{font-weight:600;font-size:26px;line-height:36px}
.hero-caption p{font-family:"Kalam",cursive;font-weight:300;font-size:29px;line-height:40px}
.slide-arrow{position:absolute;top:252px;width:30px;height:36px;background:var(--white);display:flex;align-items:center;justify-content:center}
.slide-arrow.prev{left:0;border-radius:0 4px 4px 0}
.slide-arrow.next{right:0;border-radius:4px 0 0 4px}

.section-title{font-family:"Kalam",cursive;font-size:34px;color:var(--white);font-weight:300}
.divider{width:150px;height:1px;background:#777;margin:12px 0 18px}
.center .divider{margin:12px auto 24px}
.center{text-align:center}

/* about */
.about{height:426px;background:var(--panel)}
.about .wrap{padding-top:38px;display:flex;gap:60px}
.about-text{flex:1}
.about-text p{font-size:13px;line-height:22px;color:var(--text);margin-bottom:26px}
.portrait{width:304px;height:337px;margin-top:7px;border:3px solid #ddd;background:linear-gradient(#6b5548,#2b211c)}

/* cruise */
.cruise{height:354px;background:linear-gradient(120deg,#0d1420,#1e2a3a 55%,#101822)}
.cruise .wrap{padding-top:36px;display:flex;gap:46px}
.cruise-text{flex:1}
.cruise-text h2{font-family:"Kalam",cursive;color:var(--orange);font-size:34px;font-weight:300}
.cruise-sub{font-family:"Kalam",cursive;font-weight:300;color:var(--white);font-size:24px;margin:8px 0 10px}
.cruise-sub b{font-family:"Open Sans",sans-serif;font-size:26px;font-weight:600}
.cruise-sub span{font-family:"Open Sans",sans-serif;font-size:17px;font-weight:600}
.cruise-text p{font-size:12.5px;line-height:21px;color:var(--text);margin-bottom:26px}
.video{width:346px;height:220px;margin-top:50px;border:2px solid #ccc;position:relative;background:linear-gradient(#5b8cc8,#7fb0e0 45%,#2a5f9a)}
.play{position:absolute;left:50%;top:45%;transform:translate(-50%,-50%);width:44px;height:44px;border-radius:50%;background:rgba(0,0,0,.5);display:flex;align-items:center;justify-content:center}
.video-bar{position:absolute;left:0;right:0;bottom:0;height:28px;background:#eee;display:flex;align-items:center;gap:8px;padding:0 8px;font-size:10px;color:#333}
.video-bar .track{flex:1;height:6px;background:#bbb;border-radius:3px;position:relative}
.video-bar .track i{position:absolute;left:0;top:0;bottom:0;width:12%;background:#7ab03a;border-radius:3px}
.video-bar .pbtn{width:22px;height:16px;background:#7ab03a}

/* gallery */
.gallery{height:505px;background:var(--panel-2)}
.gallery .wrap{padding-top:40px}
.grid{display:grid;grid-template-columns:325px 330px 327px;grid-template-rows:152px 146px;gap:9px 10px}
.grid div{border:2px solid #ddd}
.g1{grid-row:1/3;background:linear-gradient(#7a6a52,#3d3226)}
.g2{background:linear-gradient(#c46c1c,#5e2610)}
.g3{background:linear-gradient(#5da7d4,#c93a2c)}
.g4{background:linear-gradient(#7fb2de,#3e6f9a 60%,#2a4d70)}
.g5{background:linear-gradient(#5a3e30,#1f1612)}

/* itinerary */
.itinerary{height:615px;background:var(--black)}
.itinerary .wrap{padding-top:38px}
.route{font-size:16px;color:var(--white);margin-bottom:44px}
.itin-row{display:flex;gap:27px}
.map{width:488px;height:289px;border:3px solid #ccc;background:linear-gradient(90deg,#8ccf6b 0%,#a6dc86 55%,#dbeefa 75%)}
.schedule{width:487px;border-collapse:collapse;font-size:12.5px;color:#222;height:289px}
.schedule th,.schedule td{text-align:left}
.schedule th{background:var(--orange);color:var(--white);font-weight:600;padding:0 14px;height:34px;font-size:14px}
.schedule td{padding:0 14px;border-right:1px solid #c8c8c8}
.schedule tr:nth-child(odd) td{background:var(--row-a)}
.schedule tr:nth-child(even) td{background:var(--row-b)}
.contact-lines{margin-top:30px;font-size:14px;line-height:24px;color:var(--white)}

/* reviews */
.reviews{height:454px;background:var(--panel);position:relative;overflow:hidden}
.reviews .wrap{padding-top:36px}
.avatars{display:flex;justify-content:center;gap:20px;margin-bottom:18px}
.avatar{width:110px;height:110px;border-radius:50%;border:4px solid #e6e6e6;background:linear-gradient(#c9b8a6,#6e6e78)}
.quote-mark{font-size:48px;color:#777;line-height:40px;font-family:Georgia,serif}
.quote{font-size:12px;color:var(--text);width:880px;margin:6px auto 10px;line-height:19px}
.reviewer{color:var(--orange);font-weight:600;font-size:13px}
.wave{position:absolute;left:0;bottom:0;width:1200px;height:90px}

/* footer */
.site-footer{height:348px;background:var(--black);position:relative}
.footer-cols{display:flex;padding-top:28px}
.footer-col{width:163px}
.footer-col.contact{width:287px}
.footer-col.news{flex:1}
.footer-col h4{color:var(--white);font-size:14px;font-weight:700;margin-bottom:8px}
.footer-col h4:after{content:"";display:block;width:54px;height:2px;background:var(--orange);margin-top:6px}
.footer-col ul{list-style:none;padding-top:8px}
.footer-col li{font-size:11.5px;color:var(--muted);line-height:25px}
.footer-col li:before{content:"› ";color:var(--white)}
.footer-col p{font-size:11.5px;color:var(--muted);line-height:18px;margin-top:10px}
.footer-col .strong{color:var(--white);font-weight:700}
.ct-line{display:flex;align-items:center;gap:10px;font-size:11.5px;color:var(--muted);margin-top:14px}
.email-field{width:188px;height:28px;background:var(--white);margin-top:10px;color:#999;font-size:11px;padding:6px 8px}
.subscribe{display:inline-block;margin-top:12px;background:var(--orange);color:#111;font-weight:700;font-size:12px;padding:6px 12px}
.copyright{position:absolute;left:0;right:0;bottom:0;height:52px}
.copyright .wrap{display:flex;align-items:center;height:52px;border-top:1px solid #222;font-size:11.5px;color:var(--muted)}
.copyright .socials{margin-left:auto;display:flex;gap:8px}
</style>
</head>
<body>

<header class="site-header">
  <div class="wrap">
    <div class="brand"><span class="brand-mark"></span>Brenna Coyle's Musical Tour of Ireland</div>
    <div class="header-right">
      <div class="phone">
        <span class="phone-ico"><svg width="16" height="16" viewBox="0 0 24 24"><path fill="#f7941d" d="M6.6 10.8a15 15 0 0 0 6.6 6.6l2.2-2.2c.3-.3.7-.4 1-.2 1.1.4 2.3.6 3.6.6.6 0 1 .4 1 1V20c0 .6-.4 1-1 1A17 17 0 0 1 3 4c0-.6.4-1 1-1h3.5c.6 0 1 .4 1 1 0 1.3.2 2.5.6 3.6.1.3 0 .7-.2 1z"/></svg></span>
        01555 010234
      </div>
      <div class="follow">Follow Us : <span class="social"></span><span class="social"></span><span class="social"></span><span class="social"></span></div>
      <span class="book-btn">Booking Now</span>
    </div>
  </div>
</header>

<nav class="main-nav">
  <ul>
    <li class="current">Home</li><li>Bio</li><li>Tour dates</li><li>Brenna Coyle cruise</li><li>Musical tour of Ireland</li><li>Video</li><li>Gallery</li><li>Contact Us</li>
  </ul>
</nav>

<section class="hero" role="img" aria-label="Close-up of tin whistles and flutes in a tan and red cloth case">
  <span class="slide-arrow prev"><svg width="12" height="16" viewBox="0 0 12 16"><path d="M9 2 3 8l6 6" stroke="#333" stroke-width="2.5" fill="none"/></svg></span>
  <span class="slide-arrow next"><svg width="12" height="16" viewBox="0 0 12 16"><path d="m3 2 6 6-6 6" stroke="#333" stroke-width="2.5" fill="none"/></svg></span>
  <div class="hero-caption">
    <h1>I Am Brenna Coyle</h1>
    <p>I am an Irish musician who plays the tin whistle and the flute.</p>
  </div>
</section>

<section class="about">
  <div class="wrap">
    <div class="about-text">
      <h2 class="section-title">About <span class="accent">Brenna Coyle</span></h2>
      <div class="divider"></div>
      <p>BRENNA COYLE is regarded as one of the most admired musicians and personalities in Irish music in America. She was born in Dorchester, Boston to Irish parents, and she is the eldest of five children raised in a house always full of tunes. Her mother Maura comes from a fishing village in County Kerry and her father Declan, a celebrated fiddle player, grew up in a farming town in County Sligo. Brenna heard the finest Irish traditional music from her earliest years, listening to her father and his friends play at family gatherings, weddings and local sessions. She began taking lessons at a very young age.</p>
      <span class="btn">Read More</span>
    </div>
    <div class="portrait" role="img" aria-label="Portrait of Brenna Coyle holding a flute"></div>
  </div>
</section>

<section class="cruise">
  <div class="wrap">
    <div class="cruise-text">
      <h2>Brenna Coyle's Musical Tour Of Ireland</h2>
      <div class="cruise-sub">The Big Session On The High Seas <b>Cruise</b> <span>May 29-Jun 4, 2016</span></div>
      <p>Lorem ipsum dolor sit amet, consectetuer adipiscing elit, sed diam nonummy nibh euismod tincidunt ut laoreet dolore magna aliquam erat volutpat. Ut wisi enim ad minim veniam, quis nostrud exerci tation ullamcorper suscipit lobortis nisl ut aliquip ex ea commodo consequat. Duis autem vel eum iriure dolor in hendrerit in vulputate velit esse molestie consequat, vel illum dolore eu feugiat sed diam nonummy nibh euismod tincidunt ut laoreet dolore magna aliquam erat volutpat.</p>
      <span class="btn">Booking Now</span>
    </div>
    <div class="video" role="img" aria-label="Video still of a cruise ship at sea">
      <span class="play"><svg width="16" height="18" viewBox="0 0 16 18"><path d="M2 1v16l13-8z" fill="#fff"/></svg></span>
      <div class="video-bar"><span class="pbtn"></span><span class="track"><i></i></span><span>1:47 / 12:35</span></div>
    </div>
  </div>
</section>

<section class="gallery">
  <div class="wrap center">
    <h2 class="section-title">Our <span class="accent">Gallery</span></h2>
    <div class="divider"></div>
    <div class="grid">
      <div class="g1" role="img" aria-label="Brenna Coyle seated with a flute"></div>
      <div class="g2" role="img" aria-label="Whistles in a cloth case"></div>
      <div class="g3" role="img" aria-label="Cruise ship deck with red loungers"></div>
      <div class="g4" role="img" aria-label="Cruise ship sailing past mountains"></div>
      <div class="g5" role="img" aria-label="Ensemble performing with instruments"></div>
    </div>
  </div>
</section>

<section class="itinerary">
  <div class="wrap center">
    <h2 class="section-title">Aboard the <span class="accent">Northern Pearl</span></h2>
    <div class="divider"></div>
    <p class="route">New York To Halifa, Nova Scotia, ST. John, Bay Of Fundy, Canada, Portland, Maine, New England</p>
    <div class="itin-row">
      <div class="map" role="img" aria-label="Route map from New York to Portland, Saint John and Halifax"></div>
      <table class="schedule">
        <tr><th>Day</th><th>Port</th><th>Arrive</th><th>Depart</th></tr>
        <tr><td>Sunday</td><td>New York</td><td></td><td>4:00 AM</td></tr>
        <tr><td>Monday</td><td>At Sea</td><td></td><td></td></tr>
        <tr><td>Tueday</td><td>Halifax, Nova Scotia</td><td>9:00 AM</td><td>6:00 AM</td></tr>
        <tr><td>Wenesday</td><td>Saint John, Bay of Fundy,<br>New Brunswick</td><td>11:00 AM</td><td>7:00 AM</td></tr>
        <tr><td>Sunday</td><td>Sunday</td><td>8:00 AM</td><td>5:00 AM</td></tr>
        <tr><td>Thursday</td><td>Thursday</td><td></td><td></td></tr>
        <tr><td>Saturday</td><td>Saturday</td><td>8:00 AM</td><td></td></tr>
      </table>
    </div>
    <div class="contact-lines">
      PHONE : 1-800-555-0142 &nbsp;BOOKING INQUIRIES : <span class="accent">BOOK@BRENNACOYLEVOYAGE-EXAMPLE.COM</span><br>
      GENERAL INFORMATION : <span class="accent">INFO@BRENNACOYLEVOYAGE-EXAMPLE.COM</span>
    </div>
  </div>
</section>

<section class="reviews">
  <div class="wrap center">
    <h2 class="section-title">Customer <span class="accent">Reviews</span></h2>
    <div class="divider"></div>
    <div class="avatars">
      <span class="avatar" role="img" aria-label="Customer portrait"></span>
      <span class="avatar" role="img" aria-label="Customer portrait"></span>
      <span class="avatar" role="img" aria-label="Customer portrait"></span>
      <span class="avatar" role="img" aria-label="Customer portrait"></span>
      <span class="avatar" role="img" aria-label="Customer portrait"></span>
    </div>
    <div class="quote-mark">&ldquo;</div>
    <p class="quote">"Whenever the finest tin whistle and flute players of recent decades are named, lovers of Irish traditional music are sure to include Brenna Coyle on the list. Her playing is pure art, warm and inventive, lively and masterful. It is full of style, depth, feeling and heart."</p>
    <div class="reviewer">Dale Harmon, The Celtic Courier</div>
  </div>
  <svg class="wave" viewBox="0 0 1200 90" preserveAspectRatio="none">
    <path d="M0 20 C300 90 700 -20 1200 60 L1200 90 L0 90 Z" fill="#f7941d"/>
    <path d="M0 40 C300 100 700 10 1200 75 L1200 90 L0 90 Z" fill="#050505"/>
  </svg>
</section>

<footer class="site-footer">
  <div class="wrap footer-cols">
    <div class="footer-col"><h4>Event Info</h4><ul><li>Artists</li><li>Contact Us</li><li>Mailing List</li></ul></div>
    <div class="footer-col"><h4>Prices</h4><ul><li>Prices Per Person</li><li>What's Included?</li><li>Payment Options</li><li>Travel Insurance</li><li>Book Now!</li></ul></div>
    <div class="footer-col"><h4>FAQ</h4><ul><li>Top Questions</li><li>Before You Book</li><li>Placing Reservations</li><li>Automatic Billing</li><li>Manage Reservations</li><li>Pre-Cruise Details</li><li>Once Onboard</li></ul></div>
    <div class="footer-col contact"><h4>Contact Detail</h4>
      <p><span class="strong">Brenna Coyle's Musical Tour Of Ireland</span><br>Lorem ipsum dolor sit amet consectetuer adipiscing elit.</p>
      <div class="ct-line"><svg width="12" height="12" viewBox="0 0 24 24"><path fill="#f7941d" d="M6.6 10.8a15 15 0 0 0 6.6 6.6l2.2-2.2c.3-.3.7-.4 1-.2 1.1.4 2.3.6 3.6.6.6 0 1 .4 1 1V20c0 .6-.4 1-1 1A17 17 0 0 1 3 4c0-.6.4-1 1-1h3.5c.6 0 1 .4 1 1 0 1.3.2 2.5.6 3.6.1.3 0 .7-.2 1z"/></svg>00-1-555-010-7788</div>
      <div class="ct-line"><svg width="12" height="10" viewBox="0 0 12 10"><rect width="12" height="10" fill="#f7941d"/><path d="M0 0l6 5 6-5" stroke="#050505" fill="none"/></svg>book@brennacoylevoyage-example.com</div>
    </div>
    <div class="footer-col news"><h4>Newsletter Signup</h4>
      <p>Get latest updates by entering your email address</p>
      <div class="email-field">Email Address</div>
      <span class="subscribe">SUBSCRIBE</span>
    </div>
  </div>
  <div class="copyright">
    <div class="wrap">Copyright © 2016 Brenna Coyle's Musical Tour Of Ireland . All Rights Reserved.
      <span class="socials"><span class="social"></span><span class="social"></span><span class="social"></span><span class="social"></span></span>
    </div>
  </div>
</footer>

</body>
</html>
```